Dalvick's Business Card

I need some designs for a new business card including the new logo attached. An old example of our business card is also attached to show all the data that should be included on the new design.
**I added some more examples someone had mocked up**

Contact Information for Business Card

Should include all info on other examples uploaded.

```html
<!DOCTYPE html>
<html lang="en">
<head>
<meta charset="utf-8">
<title>Dalvick's Business Card</title>
<link href="https://fonts.googleapis.com/css2?family=Montserrat:wght@500;600;700&family=Oswald:wght@600&display=swap" rel="stylesheet">
<style>
  :root {
    --brand-blue: #0a72bf;
    --brand-red: #e8202a;
    --ink: #1d1d1f;
    --paper: #ffffff;
    --backdrop: #c9c9c9;
    --rule: #bcd3e8;
  }
  * { box-sizing: border-box; margin: 0; padding: 0; }
  html, body { width: 1200px; height: 800px; overflow: hidden; }
  body {
    background: var(--backdrop);
    font-family: "Montserrat", sans-serif;
    display: flex;
    flex-direction: column;
    align-items: center;
    justify-content: center;
    gap: 24px;
  }
  .card {
    position: relative;
    width: 630px;
    height: 360px;
    overflow: hidden;
    border-bottom: 3px solid var(--brand-red);
  }

  /* Front */
  .card--front { background: var(--paper); }
  .front-main {
    position: absolute;
    inset: 0 0 84px 0;
    display: flex;
    align-items: center;
    padding: 0 40px;
  }
  .brand {
    display: flex;
    align-items: center;
    gap: 10px;
    width: 270px;
  }
  .brand-dot {
    width: 26px; height: 26px;
    border-radius: 50%;
    background: var(--brand-red);
    flex: none;
  }
  .brand-name {
    display: block;
    font-weight: 700;
    font-size: 40px;
    color: var(--brand-blue);
    line-height: 1;
  }
  .brand-tagline {
    display: block;
    font-weight: 600;
    font-size: 8.5px;
    letter-spacing: 0.6px;
    color: var(--brand-red);
    text-transform: uppercase;
    margin-top: 4px;
  }
  .front-divider {
    width: 1px;
    height: 96px;
    background: var(--rule);
    margin: 0 26px 0 14px;
  }
  .contact-name {
    font-weight: 600;
    font-size: 25px;
    color: var(--brand-blue);
    letter-spacing: 0.5px;
    margin-bottom: 8px;
  }
  .contact-line {
    display: flex;
    align-items: center;
    gap: 10px;
    font-weight: 500;
    font-size: 15.5px;
    color: var(--ink);
    line-height: 1.5;
  }
  .contact-line svg { width: 16px; height: 16px; flex: none; }
  .front-band {
    position: absolute;
    left: 0; right: 0; bottom: 0;
    height: 84px;
    background: var(--brand-blue);
    display: flex;
  }
  .band-cell {
    flex: 1;
    display: flex;
    align-items: center;
    justify-content: center;
    color: var(--paper);
    font-weight: 700;
    font-size: 16px;
    letter-spacing: 1px;
  }
  .band-cell + .band-cell { border-left: 1px solid rgba(255,255,255,0.35); }

  /* Back */
  .card--back { background: var(--brand-blue); }
  .back-mark {
    position: absolute;
    left: -40px; top: 40px;
    width: 320px; height: 320px;
  }
  .back-mark-name {
    position: absolute;
    left: 36px; top: 150px;
    font-weight: 700;
    font-size: 38px;
    color: var(--paper);
  }
  .back-copy {
    position: absolute;
    left: 300px; right: 30px; top: 70px;
    color: var(--paper);
  }
  .back-headline {
    font-family: "Oswald", sans-serif;
    font-weight: 600;
    font-size: 27px;
    line-height: 1.18;
    text-transform: uppercase;
  }
  .back-rule {
    height: 1px;
    background: var(--paper);
    margin: 16px 0 14px;
    width: 270px;
  }
  .back-area {
    font-weight: 700;
    font-size: 19px;
    line-height: 1.3;
  }
</style>
</head>
<body>
  <section class="card card--front">
    <div class="front-main">
      <div class="brand">
        <span class="brand-dot" aria-hidden="true"></span>
        <span>
          <span class="brand-name">Dalvick's</span>
          <span class="brand-tagline">Air Conditioning &amp; Heating Service</span>
        </span>
      </div>
      <div class="front-divider"></div>
      <div class="contact">
        <p class="contact-name">MARK DALVICK</p>
        <p class="contact-line">
          <svg viewBox="0 0 16 16" aria-hidden="true"><path fill="var(--brand-red)" d="M3.6 1.2l2.3 2.6-1.3 1.8a9 9 0 0 0 5.8 5.8l1.8-1.3 2.6 2.3-1.6 2.1C7.5 14.8 1.2 8.5 1.5 2.8z"/></svg>
          555.014.2290
        </p>
        <p class="contact-line">
          <svg viewBox="0 0 16 16" aria-hidden="true"><rect x="1" y="3" width="14" height="10" fill="var(--brand-red)"/><path d="M1 3l7 6 7-6" fill="none" stroke="#fff" stroke-width="1.2"/></svg>
          hvacdalvick@mailbox.com
        </p>
      </div>
    </div>
    <div class="front-band">
      <div class="band-cell">LICENSED &amp; INSURED</div>
      <div class="band-cell">FAMILY OWNED &amp; OPERATED</div>
    </div>
  </section>

  <section class="card card--back">
    <svg class="back-mark" viewBox="0 0 320 320" aria-hidden="true">
      <circle cx="160" cy="160" r="130" fill="none" stroke="var(--brand-red)" stroke-width="18"/>
    </svg>
    <span class="back-mark-name">Dalvick's</span>
    <div class="back-copy">
      <p class="back-headline">Call today for all your<br>HVAC, refrigeration &amp;<br>plumbing needs</p>
      <div class="back-rule"></div>
      <p class="back-area">Serves Brookvale<br>IA &amp; Surrounding Areas</p>
    </div>
  </section>
</body>
</html>
```